Technology, Futuristic Innovation & Artificial Intelligence

I am looking for something with Artificial Intelligence DNA strands....
Blue, black, with white dna strands........I like clean, crisp, professional and not busy look.................................................................................................................................................................................................................................................................................................................................................................................. Thanks!

Target Market(s)

Engineers and United States Government Contractors

Industry/Entity Type

Engineering

Contact Information for Business Card

I've uploaded my logo the certification logo.

Font styles to use
Serif

Colors
3176b5
33a6d7
ffffff

Requirements
Must have
• Name
• Title
• Address
• Phone number
• website name
• certification logo
Nice to have
• Something with Artificial Intelligence DNA strands......
• **Please note it would be nice to have the business card 3D or textured with raised images. Thanks
Should not have
• Please no feminine flowery designs....this is an engineering firm

```html
<!DOCTYPE html>
<html lang="en">
<head>
<meta charset="utf-8">
<title>Novaris Business Card</title>
<link rel="stylesheet" href="https://fonts.googleapis.com/css2?family=Roboto+Condensed:wght@400;700&family=Work+Sans:wght@400;500&display=swap">
<style>
  :root {
    --navy: #0a1a3a;
    --deep: #06102a;
    --blue: #3176b5;
    --cyan: #33a6d7;
    --white: #ffffff;
    --ink: #1c1c22;
    --backdrop: #e7e4de;
  }
  * { margin: 0; padding: 0; box-sizing: border-box; }
  html, body { width: 1200px; height: 930px; overflow: hidden; }
  body { background: var(--backdrop); position: relative; }

  .card {
    position: absolute;
    left: 278px;
    width: 644px;
    height: 368px;
    border-radius: 22px;
    overflow: hidden;
    box-shadow: 0 6px 18px rgba(0,0,0,.25);
  }
  .card--front { top: 76px; }
  .card--back { top: 486px; }

  .tech-field {
    position: absolute; inset: 0;
    background:
      radial-gradient(ellipse at 35% 40%, rgba(51,166,215,.35), transparent 60%),
      radial-gradient(ellipse at 80% 70%, rgba(49,118,181,.35), transparent 55%),
      linear-gradient(160deg, var(--navy), var(--deep) 70%);
  }

  .naics {
    position: absolute; left: 31px; top: 26px;
    font: 400 21px/26px "Roboto Condensed", sans-serif;
    color: var(--white);
  }
  .cert-badge { position: absolute; left: 536px; top: 18px; }

  .brand {
    position: absolute; left: 30px; top: 112px; width: 240px;
    text-align: center; color: var(--white);
    font-family: "Roboto Condensed", sans-serif; font-weight: 700;
  }
  .brand__name { font-size: 46px; letter-spacing: 3px; line-height: 1; }
  .brand__mark { display: inline-block; width: 12px; height: 12px; background: var(--cyan); margin-right: 8px; vertical-align: 6px; }
  .brand__tag { font-size: 9px; text-align: right; margin-top: 4px; letter-spacing: .3px; }
  .motto {
    position: absolute; left: 30px; top: 211px; width: 240px; text-align: center;
    font: 400 17px "Roboto Condensed", sans-serif; color: var(--white);
  }

  .wave { position: absolute; inset: 0; }

  .contact {
    position: absolute; right: 29px; top: 196px; text-align: right;
    font-family: "Work Sans", sans-serif; color: var(--ink);
  }
  .contact__name { font-size: 24px; font-weight: 500; letter-spacing: .3px; line-height: 30px; }
  .contact__title { font-size: 15px; line-height: 18px; margin-bottom: 8px; }
  .contact__line { font-size: 16px; line-height: 20px; }
  .contact__row { font-size: 16px; line-height: 21px; display: flex; justify-content: flex-end; align-items: center; gap: 8px; }
  .contact__row svg { width: 10px; height: 10px; }
  .contact__gap { height: 4px; }

  .ids {
    position: absolute; left: 31px; top: 31px;
    font: 400 18px/23px "Work Sans", sans-serif; color: var(--white);
  }
  .brand-large {
    position: absolute; left: 40px; top: 186px; width: 250px; text-align: center;
    font: 700 50px/1 "Roboto Condensed", sans-serif; letter-spacing: 3px; color: var(--white);
  }
  .divider { position: absolute; left: 312px; top: 128px; width: 2px; height: 173px; background: var(--white); }
  .services {
    position: absolute; left: 342px; top: 124px; list-style: none;
    font: 700 17px/23.2px "Roboto Condensed", sans-serif; color: var(--white);
  }
</style>
</head>
<body>

<section class="card card--front">
  <div class="tech-field" role="img" aria-label="Dark blue circuit board pattern background"></div>

  <p class="naics">NAICS: 541310, 541330, 541340, 541611, 541614, 541618,<br>541715, 541990, 561110, 561312, 561320, 561330, 561410</p>

  <svg class="cert-badge" width="76" height="76" viewBox="0 0 76 76" role="img" aria-label="Federal contractor verified vendor certification badge">
    <circle cx="38" cy="38" r="35" fill="#f2c230"/>
    <circle cx="38" cy="38" r="29" fill="#b8202e"/>
  </svg>

  <div class="brand">
    <div class="brand__name"><span class="brand__mark"></span>NOVARIS</div>
    <div class="brand__tag">BRINGING TOMORROW TODAY</div>
  </div>
  <p class="motto">spiritus est in terra nostra</p>

  <svg class="wave" viewBox="0 0 644 368" preserveAspectRatio="none">
    <!-- upper thin swooshes on the dark field -->
    <path d="M0,258 C110,296 220,282 318,226" fill="none" stroke="#ffffff" stroke-width="3"/>
    <path d="M430,164 C500,134 580,128 625,158" fill="none" stroke="#ffffff" stroke-width="3"/>
    <!-- white lower area -->
    <path d="M0,268 C120,302 260,272 360,200 C440,152 540,136 644,168 L644,368 L0,368 Z" fill="#ffffff"/>
    <!-- dark bands layered inside the white area -->
    <path d="M0,278 C120,312 250,286 350,222 C390,198 420,184 450,174" fill="none" stroke="#0a1a3a" stroke-width="6" stroke-linecap="round"/>
    <path d="M40,322 C160,326 260,296 350,244" fill="none" stroke="#0a1a3a" stroke-width="4" stroke-linecap="round"/>
  </svg>

  <div class="contact">
    <div class="contact__name">DANA WHITCOMB</div>
    <div class="contact__title">CEO</div>
    <div class="contact__line">1820 Harborline Drive</div>
    <div class="contact__line">Marlow, SC 29401</div>
    <div class="contact__gap"></div>
    <div class="contact__row">843.555.0147
      <svg viewBox="0 0 10 10"><path d="M2,1 L4,1 L5,3 L4,4 C4.5,5.5 5,6 6,6.5 L7,5.5 L9,6.5 L9,8.5 C5,9 1,5 2,1 Z" fill="#1c1c22"/></svg>
    </div>
    <div class="contact__row">dwhitcomb@novaris-eng.org
      <svg viewBox="0 0 10 10"><rect x="1" y="2.5" width="8" height="5.5" fill="none" stroke="#1c1c22"/><path d="M1,2.5 L5,6 L9,2.5" fill="none" stroke="#1c1c22"/></svg>
    </div>
    <div class="contact__row">www.novaris-eng.org
      <svg viewBox="0 0 10 10"><circle cx="5" cy="5" r="4" fill="none" stroke="#1c1c22"/><path d="M1,5 H9 M5,1 V9" stroke="#1c1c22"/><ellipse cx="5" cy="5" rx="2" ry="4" fill="none" stroke="#1c1c22"/></svg>
    </div>
  </div>
</section>

<section class="card card--back">
  <div class="tech-field" role="img" aria-label="Dark blue circuit board pattern background"></div>

  <p class="ids">DUNS #012345678<br>Cage #4QXT9<br>EDMWOSB</p>

  <div class="brand-large">NOVARIS</div>

  <div class="divider"></div>

  <ul class="services">
    <li>PROGRAM MANAGEMENT</li>
    <li>SYSTEMS ENGINEERING</li>
    <li>SYSTEMS INTEGRATION</li>
    <li>CYBER SECURITY</li>
    <li>INFORMATION TECHNOLOGY</li>
    <li>SOFTWARE DEVELOPMENT</li>
    <li>ARTIFICIAL INTELLIGENCE ENGINEERING</li>
    <li>DODAF Architecture of Complex Systems</li>
  </ul>
</section>

</body>
</html>
```